Moxy Fen needs some awesome stationary

Do you have what it takes to get my brand? You either do or you don't, have a crack at a design and you my just win my business.

I don't want to waste your or my time, so put your creative genius on either a business card or envelope.

I however need a package of stationary that follows the same brand. I will message you to complete the remaining should I like your first submission.

Here is what I need, have a go!

Basically I need the following for my small business based in melbourne.
- Letterhead (printer ready and MS Word)
- Business Card
- Compliments Slip
- Envelope
- Proposal Cover Page (MS Word only)
- Presentation Folder
- Marbled Fox Cards
- Student Name Tent
- Index Cards
- Vell-Ka

I am establishing the brand and it must be modern, professional but also relaxed; that is not formal and not corporate. It represents a company are leaders, but small enough to care and operate like a bunch of friends. We are bringing people and conversations back to business, and turfing out all the bureaucracy and crazy and wasteful procedures. Its about "lets talk and figure it out together and find even better ways".

Target Market(s)

Mainly companies that build software products, but Agile practices are used in many other industries (even graphic design projects)

Industry/Entity Type

Information Technology

Font styles to use
Sans Serif

Colors
3176b5
aaaaaa

Requirements
Must have
• I like curves and circles and not boxes or rectangles.
• I want a colour rich design with my brand colours, but it must be balanced.
• I want more modern than traditional, but simple modern
Should not have
• Not corporate
• Please don't waste my time if your not going to think about it.
• Don't mess with my primary logo
• Don't change my colours
• Don't overlay logo on image

```html
<!DOCTYPE html>
<html lang="en">
<head>
<meta charset="utf-8">
<title>Moxy Fen — Business Card</title>
<link rel="stylesheet" href="https://fonts.googleapis.com/css2?family=Open+Sans:wght@400;600;700&display=swap">
<style>
  :root {
    --brand-blue: #3176b5;
    --blue-light: #4a86c8;
    --blue-deep: #1d55a0;
    --band-blue: #1f4f9a;
    --brand-grey: #aaaaaa;
    --slate: #9aa4b2;
    --paper: #f4f5f6;
    --map-faint: #e6e8ea;
    --stage: #9cc8dc;
    --white: #ffffff;
  }
  * { margin: 0; padding: 0; box-sizing: border-box; }
  html, body { width: 1200px; height: 856px; overflow: hidden; }
  body {
    background: var(--stage);
    font-family: "Open Sans", sans-serif;
    position: relative;
  }
  .card {
    position: absolute;
    width: 540px;
    height: 309px;
    border-radius: 26px;
    overflow: hidden;
    box-shadow: 0 10px 28px rgba(20, 60, 100, 0.25);
  }
  .card-front { left: 40px; top: 274px; background: linear-gradient(160deg, var(--blue-light), var(--blue-deep)); }
  .card-back  { left: 620px; top: 274px; background: var(--paper); }
  .card svg.shapes { position: absolute; inset: 0; width: 100%; height: 100%; }
  .map-area { position: absolute; border-radius: 40px; }
  .card-front .map-area { left: 120px; top: 40px; width: 380px; height: 200px; background: rgba(255,255,255,0.05); }
  .card-back .map-area { left: 150px; top: 60px; width: 300px; height: 120px; background: var(--map-faint); opacity: 0.6; }

  .front-wordmark {
    position: absolute; left: 245px; top: 80px; width: 295px;
    text-align: center; color: var(--white);
    font-weight: 600; font-size: 34px; letter-spacing: 0.5px;
  }

  .back-wordmark {
    position: absolute; left: 36px; top: 40px;
    display: flex; align-items: center; gap: 10px;
  }
  .back-wordmark .dot { width: 34px; height: 34px; border-radius: 50%; background: var(--brand-blue); }
  .back-wordmark .name { color: var(--brand-blue); font-weight: 600; font-size: 20px; }

  .person {
    position: absolute; left: 330px; top: 42px; width: 200px; color: var(--white);
  }
  .person .full-name { font-weight: 700; font-size: 14px; letter-spacing: 1.6px; }
  .person .role { font-size: 8px; margin-top: 1px; }

  .address {
    position: absolute; left: 30px; top: 183px;
    color: var(--band-blue); font-size: 10px;
  }
  .contacts {
    position: absolute; left: 34px; top: 226px;
    display: grid; grid-template-columns: 150px 170px; row-gap: 5px;
    color: var(--white); font-size: 10px;
  }
  .contacts .item { display: flex; align-items: center; gap: 6px; }
  .contacts svg { width: 10px; height: 10px; flex: none; }
</style>
</head>
<body>

  <section class="card card-front" aria-label="Business card front">
    <div class="map-area" role="img" aria-label="Faint world map backdrop"></div>
    <svg class="shapes" viewBox="0 0 540 309" aria-hidden="true">
      <path d="M262 70 L540 50 L540 118 L246 134 Z" fill="var(--band-blue)" opacity="0.85"/>
      <circle cx="165" cy="218" r="56" fill="var(--white)"/>
    </svg>
    <div class="front-wordmark">Moxy Fen</div>
  </section>

  <section class="card card-back" aria-label="Business card back">
    <div class="map-area" role="img" aria-label="Faint world map backdrop"></div>
    <svg class="shapes" viewBox="0 0 540 309" aria-hidden="true">
      <path d="M332 36 L540 26 L540 76 L320 84 Q314 84 318 76 Z" fill="var(--brand-blue)"/>
      <path d="M420 176 L540 158 L540 309 L420 309 Z" fill="var(--slate)"/>
      <path d="M0 210 L440 190 Q460 189 462 200 L470 240 L470 309 L0 309 Z" fill="var(--brand-blue)"/>
    </svg>

    <div class="back-wordmark">
      <span class="dot"></span>
      <span class="name">Moxy Fen</span>
    </div>

    <div class="person">
      <div class="full-name">DARA QUILLON</div>
      <div class="role">Founder, Agile Coach</div>
    </div>

    <p class="address">PO Box 4187, Fernleigh Vale, VIC 3199, Australia</p>

    <div class="contacts">
      <div class="item">
        <svg viewBox="0 0 10 10"><path d="M1 3 Q5 0 9 3 L8 5 L6 4 L6 3 L4 3 L4 4 L2 5 Z" fill="var(--white)"/><rect x="2" y="6" width="6" height="3" fill="var(--white)"/></svg>
        <span>1300MOXYF</span>
      </div>
      <div class="item">
        <svg viewBox="0 0 10 10"><rect x="1" y="2" width="8" height="6" fill="none" stroke="var(--white)"/><path d="M1 2 L5 6 L9 2" fill="none" stroke="var(--white)"/></svg>
        <span>dara@moxy-fen.com.au</span>
      </div>
      <div class="item">
        <svg viewBox="0 0 10 10"><rect x="3" y="1" width="4" height="8" rx="1" fill="var(--white)"/></svg>
        <span>+61 400 555 012</span>
      </div>
      <div class="item">
        <svg viewBox="0 0 10 10"><circle cx="5" cy="5" r="4" fill="none" stroke="var(--white)"/><path d="M1 5 H9 M5 1 Q2 5 5 9 Q8 5 5 1" fill="none" stroke="var(--white)" stroke-width="0.8"/></svg>
        <span>www.moxy-fen.com.au</span>
      </div>
    </div>
  </section>

</body>
</html>
```